Stationery for Villa Marenta Design Hotel**

Who we are:

Wander on an isolated beach while breathing in the fresh, salty, sea air. Listen to the warm Pacific wind rustling through green palm trees as you walk to a pristine lagoon. Feel the delicious warmth of the sun kiss your skin; the beach is yours. At Villa Marenta you can experience a vacation in undisturbed, natural beauty. We have created a place for you to find new strength, relaxation, and inner harmony. We offer total rest to the experienced traveler from all over the world.

We are a brand new and smartly built design-hotel (under construction) close to a unique beach and a fantastic surf spot in Huatulco, Southwest Mexico.

As you can see in the attachments, we do have an established corporate design, but as for now still need a format for booklets for information around our hotel and things to do in the area, important numbers (we fill in the content for that one).

Our corporate colors:
green #64b445, brown #b07043, blue #0ab7cf, yellow # f9b02a and #fcc01a, navy #444f69
Corporate fonts:
Krub and Miller Banner.
For further information access:
www.villamarenta.example
https://slidevault.example/view/QmPxLwZrTyKsNbVcHdJe/

Social Media: VillaMarenta

Industry/Entity Type

Hotel

Font styles to use
Other font styles liked:
• Krub, Miller Banner

Requirements
Must have
• Stick to Logo Design, defined corporate elements, logo, colors, fonts and general touch and feel
Nice to have
• Who we are:

Our corporate colors:
Corporate fonts:
Krub and Miller Banner.
www.villamarenta.example

Social Media: VillaMarenta

```html
<!DOCTYPE html>
<html lang="en">
<head>
<meta charset="utf-8">
<title>Villa Marenta Design Hotel – Business Card</title>
<link rel="stylesheet" href="https://fonts.googleapis.com/css2?family=Open+Sans:wght@400;700&family=Gelasio:wght@400&family=Krub:wght@500&display=swap">
<style>
  :root {
    --page: #e6e7ea;
    --card-dark: #3b3c3e;
    --card-darker: #2a2b2d;
    --hatch: #323335;
    --paper: #ffffff;
    --gold: #e3a718;
    --blue: #3aa6dc;
    --blue-light: #5bbbe8;
    --ink: #555659;
    --muted: #8a8b8e;
    --rule-dark: #2f3033;
  }
  * { box-sizing: border-box; margin: 0; padding: 0; }
  html, body { width: 1200px; height: 900px; overflow: hidden; }
  body {
    background: var(--page);
    display: flex; flex-direction: column; align-items: center; justify-content: center;
    gap: 50px;
  }
  .card {
    position: relative; width: 720px; height: 400px;
    border-radius: 28px; overflow: hidden;
    box-shadow: 0 10px 28px rgba(0,0,0,.18);
  }
  .hatch {
    position: absolute;
    background: repeating-linear-gradient(135deg, var(--hatch) 0 3px, var(--card-dark) 3px 6px);
  }
  .brand {
    display: flex; flex-direction: column; align-items: center; gap: 14px;
    font-family: "Krub", sans-serif; font-weight: 500; color: var(--gold);
    letter-spacing: .08em; text-transform: uppercase; white-space: nowrap;
  }
  .brand-mark { width: 70px; height: 70px; border: 3px solid var(--gold); }

  /* Front */
  .card-front { background: var(--paper); }
  .front-panel {
    position: absolute; left: 0; top: 0; bottom: 0; width: 270px;
    background: var(--card-dark);
    display: flex; align-items: center; justify-content: center;
  }
  .front-panel .hatch { left: 0; right: 0; height: 26px; }
  .front-panel .hatch.top { top: 30px; }
  .front-panel .hatch.bottom { bottom: 30px; }
  .front-panel .brand { font-size: 22px; }
  .identity { position: absolute; left: 315px; top: 48px; width: 300px; }
  .person-name {
    font-family: "Open Sans", sans-serif; font-weight: 700;
    font-size: 34px; color: var(--gold); line-height: 1.1; white-space: nowrap;
  }
  .person-role {
    font-family: "Open Sans", sans-serif; font-weight: 400;
    font-size: 19px; color: var(--muted); margin-top: 2px;
  }
  .role-rule { display: flex; height: 4px; margin-top: 8px; width: 300px; }
  .role-rule span:first-child { width: 30%; background: var(--rule-dark); }
  .role-rule span:last-child { flex: 1; background: var(--blue); }
  .contacts { list-style: none; margin-top: 22px; }
  .contacts li {
    display: flex; align-items: flex-start; gap: 12px;
    font-family: "Gelasio", serif; font-size: 19px; color: var(--ink); line-height: 1.35;
    margin-bottom: 4px; white-space: nowrap;
  }
  .contacts svg { flex: none; margin-top: 5px; }
  .front-accent {
    position: absolute; right: 0; bottom: 0; width: 110px; height: 150px;
    background: linear-gradient(160deg, var(--blue-light), var(--blue));
  }
  .front-notch { position: absolute; right: 0; top: 190px; width: 36px; height: 36px; background: var(--card-dark); }

  /* Back */
  .card-back { background: var(--card-dark); }
  .back-frame {
    position: absolute; left: 26px; top: 26px; right: 64px; bottom: 90px;
    border: 6px solid var(--card-darker);
  }
  .card-back .hatch.side { right: 0; top: 0; bottom: 0; width: 40px; }
  .back-band {
    position: absolute; left: 0; right: 0; bottom: 0; height: 74px;
    background: linear-gradient(180deg, var(--blue-light), var(--blue));
    display: flex; align-items: center; justify-content: center;
    font-family: "Gelasio", serif; font-size: 24px; color: var(--paper); letter-spacing: .03em;
  }
  .back-brand { position: absolute; left: 0; right: 40px; top: 60px; bottom: 74px;
    display: flex; align-items: center; justify-content: center; }
  .back-brand .brand { font-size: 28px; }
</style>
</head>
<body>

<section class="card card-front" aria-label="Business card front">
  <div class="front-panel">
    <div class="hatch top"></div>
    <div class="hatch bottom"></div>
    <div class="brand"><span class="brand-mark"></span><span>Villa Marenta</span></div>
  </div>
  <div class="identity">
    <h1 class="person-name">Example Name</h1>
    <p class="person-role">Designation</p>
    <div class="role-rule"><span></span><span></span></div>
    <ul class="contacts">
      <li>
        <svg width="18" height="18" viewBox="0 0 18 18" aria-hidden="true"><rect width="18" height="18" rx="2" fill="#e3a718"/><path d="M9 3.5a3.5 3.5 0 0 0-3.5 3.5c0 2.6 3.5 6.5 3.5 6.5s3.5-3.9 3.5-6.5A3.5 3.5 0 0 0 9 3.5zm0 4.8a1.3 1.3 0 1 1 0-2.6 1.3 1.3 0 0 1 0 2.6z" fill="#fff"/></svg>
        <span>Villa Marenta, Playa Serena,<br>Puerto Alba, Costa Verde, Lunaria</span>
      </li>
      <li>
        <svg width="18" height="18" viewBox="0 0 18 18" aria-hidden="true"><rect width="18" height="18" rx="2" fill="#e3a718"/><path d="M6 4l2 2.4-1.2 1.4a6.5 6.5 0 0 0 3.4 3.4L11.6 10 14 12l-1.3 1.8C8.5 13.6 4.4 9.5 4.2 5.3z" fill="#fff"/></svg>
        <span>+52 (555) 014 7392</span>
      </li>
      <li>
        <svg width="18" height="18" viewBox="0 0 18 18" aria-hidden="true"><rect width="18" height="18" rx="2" fill="#e3a718"/><rect x="4" y="5.5" width="10" height="7" fill="none" stroke="#fff" stroke-width="1.3"/><path d="M4 5.5l5 4 5-4" fill="none" stroke="#fff" stroke-width="1.3"/></svg>
        <span>hello@villamarenta.example</span>
      </li>
      <li>
        <svg width="18" height="18" viewBox="0 0 18 18" aria-hidden="true"><rect width="18" height="18" rx="2" fill="#e3a718"/><circle cx="9" cy="9" r="4.8" fill="none" stroke="#fff" stroke-width="1.2"/><ellipse cx="9" cy="9" rx="2" ry="4.8" fill="none" stroke="#fff" stroke-width="1.1"/><path d="M4.2 9h9.6" stroke="#fff" stroke-width="1.1"/></svg>
        <span>www.villamarenta.example</span>
      </li>
    </ul>
  </div>
  <div class="front-notch"></div>
  <div class="front-accent"></div>
</section>

<section class="card card-back" aria-label="Business card back">
  <div class="back-frame"></div>
  <div class="hatch side"></div>
  <div class="back-brand">
    <div class="brand"><span class="brand-mark"></span><span>Villa Marenta</span></div>
  </div>
  <div class="back-band">www.villamarenta.example</div>
</section>

</body>
</html>
```